Restaurant Finder Website Design

I need to create a website that will help people find restaurants around a zip code or address.

I would like to have a very clean and simple design. I will need a design for the homepage, that should be very clean and simple to use. its where the users will launch their search. I am thinking something like tavuro like.. big search field with a very clean page where users can create an account or restaurants subscribe to the service.

Also need the design of the search results page, I would like to display a big map with the results and a list on the side or the bottom of the map.

Also need a profile page for the users that sign up to the site.

Mostly what I need are guidelines and color coordinated elements, like a general layout and buttons that work together. I would like to know what the action buttons and elements should look like. Because its going to have some more detail pages.

Target Market(s)

People in general, mainly people that work at an office and have to find a place for lunch every day.

Industry/Entity Type

Restaurant

Number of Pages Required

4 page

Font styles to use
Serif
Sans Serif

Requirements
Must have
• It must be a really simple and clean design but look edgy.

```html
<!DOCTYPE html>
<html lang="en">
<head>
<meta charset="utf-8">
<title>Forkspot — Find the best restaurants</title>
<link rel="stylesheet" href="https://fonts.googleapis.com/css2?family=Open+Sans:wght@400;600&display=swap">
<style>
  :root {
    --brand-red: #c62027;
    --ink: #111111;
    --logo-ink: #353a45;
    --chip-grey: #c8c8c8;
    --field-text: #8a8a8a;
    --icon-grey: #8d8d8d;
    --white: #ffffff;
    --black: #000000;
  }
  * { box-sizing: border-box; margin: 0; padding: 0; }
  html, body { width: 1200px; height: 709px; overflow: hidden; }
  body {
    position: relative;
    background: var(--white);
    font-family: "Open Sans", Arial, sans-serif;
    color: var(--ink);
  }
  .top-nav { position: absolute; top: 30px; left: 872px; display: flex; gap: 10px; }
  .nav-chip {
    height: 33px; padding: 0 11px; border-radius: 3px;
    background: var(--chip-grey); color: var(--white);
    font-size: 12px; line-height: 33px; text-decoration: none; white-space: nowrap;
  }
  .brand {
    position: absolute; top: 212px; left: 0; width: 1200px;
    display: flex; justify-content: center; align-items: center; gap: 12px;
  }
  .brand-dot { width: 64px; height: 64px; border-radius: 50%; background: var(--brand-red); }
  .brand-name { font-size: 38px; font-weight: 600; color: var(--logo-ink); letter-spacing: -0.5px; }
  .tagline {
    position: absolute; top: 296px; width: 1200px; text-align: center;
    font-size: 22px; font-weight: 400; color: var(--ink);
  }
  .search-band {
    position: absolute; left: 61px; top: 344px; width: 1079px; height: 286px;
    background: var(--brand-red);
  }
  .search-form { position: absolute; left: 82px; top: 34px; display: flex; height: 63px; }
  .search-field {
    display: flex; align-items: center; gap: 9px; width: 354px; padding-left: 16px;
    background: var(--white); color: var(--field-text); font-size: 12px;
  }
  .search-field + .search-field { border-left: 1px solid #d6d6d6; width: 353px; }
  .search-button {
    position: relative; width: 209px; background: var(--black); color: var(--white);
    border: 0; font-family: inherit; font-size: 22px; font-weight: 600;
  }
  .search-button::before {
    content: ""; position: absolute; left: -9px; top: 50%; margin-top: -7px;
    border-style: solid; border-width: 7px 9px 7px 0;
    border-color: transparent var(--black) transparent transparent;
  }
  .create-account {
    position: absolute; left: 470px; top: 127px; width: 139px; height: 36px;
    background: var(--white); border-radius: 3px; color: var(--ink);
    font-size: 13px; line-height: 36px; text-align: center; text-decoration: none;
  }
  .map-links {
    position: absolute; top: 196px; left: 0; width: 100%;
    display: flex; justify-content: center; gap: 26px;
  }
  .map-link {
    display: flex; align-items: center; gap: 9px;
    color: var(--white); font-size: 13px; text-transform: uppercase; text-decoration: none;
  }
  .map-link-mark { width: 24px; height: 24px; border-radius: 50%; background: var(--black); }
  .audience-note {
    position: absolute; top: 236px; width: 100%; text-align: center;
    color: var(--white); font-size: 19px;
  }
  .site-footer {
    position: absolute; left: 0; bottom: 0; width: 1200px; height: 33px;
    background: var(--black); color: var(--white);
    font-size: 12px; font-weight: 600; line-height: 33px; text-align: center;
  }
</style>
</head>
<body>
  <nav class="top-nav">
    <a class="nav-chip" href="#">Order Food</a>
    <a class="nav-chip" href="#">Book A Table</a>
    <a class="nav-chip" href="#">Log In</a>
  </nav>

  <div class="brand">
    <span class="brand-dot"></span>
    <span class="brand-name">Forkspot</span>
  </div>

  <h1 class="tagline">Find the best restaurants, cafes, and bars in Delhi NCR</h1>

  <section class="search-band">
    <form class="search-form">
      <label class="search-field">
        <svg width="22" height="30" viewBox="0 0 22 30" aria-hidden="true">
          <path d="M11 2a9 9 0 0 0-9 9c0 7 9 17 9 17s9-10 9-17a9 9 0 0 0-9-9z" fill="none" stroke="var(--icon-grey)" stroke-width="2"/>
          <circle cx="11" cy="11" r="4" fill="none" stroke="var(--icon-grey)" stroke-width="2"/>
        </svg>
        Select City
      </label>
      <label class="search-field">
        <svg width="16" height="26" viewBox="0 0 16 26" aria-hidden="true">
          <rect x="1" y="1" width="14" height="24" fill="var(--icon-grey)"/>
          <g fill="var(--white)">
            <rect x="4" y="4" width="3" height="3"/><rect x="9" y="4" width="3" height="3"/>
            <rect x="4" y="10" width="3" height="3"/><rect x="9" y="10" width="3" height="3"/>
            <rect x="4" y="16" width="3" height="3"/><rect x="9" y="16" width="3" height="3"/>
          </g>
        </svg>
        zip code
      </label>
      <button class="search-button" type="button">SEARCH</button>
    </form>

    <a class="create-account" href="#">Create Account</a>

    <div class="map-links">
      <a class="map-link" href="#"><span class="map-link-mark"></span>Use Plotmark Map</a>
      <a class="map-link" href="#"><span class="map-link-mark"></span>I Have A Plotmark</a>
    </div>

    <p class="audience-note">30 Million Foodies use Forkspot Every Month</p>
  </section>

  <footer class="site-footer">2016 Copyright Forkspot. All Rights Reserved</footer>
</body>
</html>
```